i need a business card for a plumbing company in california

we are a drain cleaning , maintenance plumbing company who is starting new marketing campaign for a tatrench-less pipe installation department .

Target Market(s)

the professional who appreciates time and quality workmanship.

Industry/Entity Type

Plumbing

Colors
0655a3
ec1f27

Requirements
Must have
• the second logo needs to be included
Nice to have
• a focus on the services offered
Should not have
• any underlined words on the brief

```html
<!DOCTYPE html>
<html lang="en">
<head>
<meta charset="utf-8">
<title>Pipeline Pros Plus — Business Card</title>
<link rel="stylesheet" href="https://fonts.googleapis.com/css2?family=Ubuntu:ital,wght@0,400;0,500;0,700;1,400;1,700&display=swap">
<style>
  :root {
    --brand-blue: #0655a3;
    --brand-red: #ec1f27;
    --charcoal: #2e2e2e;
    --charcoal-light: #3b3b3b;
    --logo-grey: #77776d;
    --ink: #333333;
    --paper: #f7f7f7;
    --backdrop: #d9d9d9;
  }
  * { box-sizing: border-box; margin: 0; padding: 0; }
  html, body { width: 1200px; height: 1200px; overflow: hidden; }
  body {
    background: var(--backdrop);
    font-family: "Ubuntu", sans-serif;
    position: relative;
  }
  .card {
    position: absolute;
    left: 199px;
    width: 803px;
    height: 472px;
    background: var(--paper);
    overflow: hidden;
    box-shadow: 0 18px 30px rgba(0,0,0,0.25);
  }
  .card--front { top: 70px; }
  .card--back { top: 640px; }

  .card__art { position: absolute; inset: 0; }

  .brand-name {
    position: absolute;
    display: flex;
    align-items: center;
    gap: 10px;
    color: var(--logo-grey);
    font-weight: 700;
    font-size: 38px;
    line-height: 39px;
  }
  .brand-name__mark {
    width: 44px; height: 44px;
    border-radius: 50%;
    background: var(--brand-red);
    flex: none;
  }
  .card--front .brand-name { left: 40px; top: 196px; }
  .card--back .brand-name { left: 470px; top: 58px; }

  .tagline {
    position: absolute;
    left: 380px; width: 390px;
    top: 168px;
    text-align: center;
    font-style: italic;
  }
  .tagline__lead { display: block; color: #fff; font-size: 36px; font-weight: 400; }
  .tagline__accent { display: block; color: var(--brand-red); font-size: 62px; font-weight: 700; line-height: 64px; margin-top: -4px; }
  .tagline__accent small { font-size: 30px; }

  .services {
    position: absolute;
    left: 360px; width: 430px;
    top: 357px;
    color: #e6e6e6;
    font-size: 18px;
    line-height: 24.5px;
    text-align: center;
  }
  .services em { font-style: italic; }

  .side-bar {
    position: absolute; left: 0; top: 0; bottom: 0;
    width: 33px; background: var(--brand-blue);
  }
  .person { position: absolute; left: 53px; top: 60px; }
  .person__name { color: var(--brand-red); font-size: 43px; font-weight: 700; }
  .person__role { color: var(--ink); font-style: italic; font-size: 26px; margin-left: 26px; margin-top: -2px; }

  .contact { position: absolute; left: 33px; top: 174px; list-style: none; }
  .contact__row { display: flex; align-items: center; height: 40px; margin-bottom: 4.5px; }
  .contact__icon {
    width: 44px; height: 38px;
    background: var(--brand-red);
    border-radius: 0 5px 5px 0;
    display: flex; align-items: center; justify-content: center;
  }
  .contact__text { margin-left: 19px; color: var(--ink); font-size: 20px; font-weight: 500; }

  .social-bar {
    position: absolute; left: 33px; top: 331px;
    width: 608px; height: 52px;
    background: var(--brand-blue);
    border-radius: 0 26px 26px 0;
    display: flex; align-items: center;
  }
  .social-bar__handle { color: #fff; font-size: 19px; margin-left: 34px; width: 259px; }
  .social-bar__divider { width: 2px; height: 30px; background: #fff; margin-right: 16px; }
  .social-bar__dot { width: 36px; height: 36px; border-radius: 50%; background: #fff; margin-right: 14px; }
  .social-bar__badge { width: 22px; height: 32px; border-radius: 3px; background: #fff; margin-left: 14px; }

  .channel { position: absolute; left: 42px; top: 392px; display: flex; align-items: center; }
  .channel__mark { width: 32px; height: 32px; background: #1a1a1a; border-radius: 5px; }
  .channel__name { margin-left: 15px; color: var(--ink); font-size: 19px; }
</style>
</head>
<body>

<section class="card card--front" aria-label="Card front">
  <svg class="card__art" viewBox="0 0 803 472" preserveAspectRatio="none" aria-hidden="true">
    <defs>
      <linearGradient id="charcoal-fade" x1="0" y1="0" x2="1" y2="1">
        <stop offset="0" stop-color="#262626"/>
        <stop offset="0.55" stop-color="#3a3a3a"/>
        <stop offset="1" stop-color="#2c2c2c"/>
      </linearGradient>
    </defs>
    <rect width="803" height="472" fill="url(#charcoal-fade)"/>
    <path d="M0 0 L258 0 Q482 238 312 472 L0 472 Z" fill="#ec1f27"/>
    <path d="M0 0 L240 0 Q464 238 298 472 L0 472 Z" fill="#0655a3"/>
    <path d="M0 0 L224 0 Q446 238 287 472 L0 472 Z" fill="#f7f7f7"/>
    <path d="M803 136 L782 136 Q772 136 772 146 L772 326 Q772 336 782 336 L803 336 Z" fill="#0655a3"/>
  </svg>

  <div class="brand-name">
    <span>Pipeline<br>Pros Plus</span>
    <span class="brand-name__mark"></span>
  </div>

  <h1 class="tagline">
    <span class="tagline__lead">Lead by</span>
    <span class="tagline__accent">Example<small>...</small></span>
  </h1>

  <p class="services">
    Virgin Trench-Less Installs &amp; Replacements -<br>
    Pipe Bursting &amp; Pipe Piercing Install,<br>
    Replace, Pipe Enlargement&nbsp; <em>PULL &amp; GO</em>
  </p>
</section>

<section class="card card--back" aria-label="Card back">
  <div class="side-bar"></div>

  <div class="person">
    <h2 class="person__name">Marco Ellison</h2>
    <p class="person__role">Owner</p>
  </div>

  <div class="brand-name">
    <span>Pipeline<br>Pros Plus</span>
    <span class="brand-name__mark"></span>
  </div>

  <ul class="contact">
    <li class="contact__row">
      <span class="contact__icon">
        <svg width="20" height="20" viewBox="0 0 24 24" aria-hidden="true"><path d="M7 2 L10 7 L8 9 Q10 14 15 16 L17 14 L22 17 L20 21 Q10 22 3 9 Q3 4 7 2 Z" fill="#fff"/></svg>
      </span>
      <span class="contact__text">2095550142</span>
    </li>
    <li class="contact__row">
      <span class="contact__icon">
        <svg width="22" height="16" viewBox="0 0 24 16" aria-hidden="true"><rect x="1" y="1" width="22" height="14" fill="none" stroke="#fff" stroke-width="2"/><path d="M1 1 L12 9 L23 1" fill="none" stroke="#fff" stroke-width="2"/></svg>
      </span>
      <span class="contact__text">info@PipelineProsPlus.com</span>
    </li>
    <li class="contact__row">
      <span class="contact__icon">
        <svg width="20" height="20" viewBox="0 0 24 24" aria-hidden="true" fill="none" stroke="#fff" stroke-width="1.8"><circle cx="12" cy="12" r="10"/><ellipse cx="12" cy="12" rx="4.5" ry="10"/><path d="M2 12 H22 M4 7 H20 M4 17 H20"/></svg>
      </span>
      <span class="contact__text">www.PipelineProsPlus.com</span>
    </li>
  </ul>

  <div class="social-bar">
    <span class="social-bar__handle">/social@PipelineProsPlus</span>
    <span class="social-bar__divider"></span>
    <span class="social-bar__dot"></span>
    <span class="social-bar__dot"></span>
    <span class="social-bar__dot"></span>
    <span class="social-bar__dot"></span>
    <span class="social-bar__badge"></span>
  </div>

  <div class="channel">
    <span class="channel__mark"></span>
    <span class="channel__name">PipelineProsPlus</span>
  </div>
</section>

</body>
</html>
```